Tiskoro

We need a business card for our company is a holding for different business all are different we try to have some air of relax and fun in our projects we add pictures of the office to give you an idea od the mood of the business

Business

```html
<!DOCTYPE html>
<html lang="en">
<head>
<meta charset="utf-8">
<title>Tiskoro – Business Card</title>
<link href="https://fonts.googleapis.com/css2?family=Archivo:wght@800&family=Short+Stack&display=swap" rel="stylesheet">
<style>
  :root {
    --stage: #4a4a4a;
    --card-black: #1e1e1e;
    --card-white: #ffffff;
    --name-yellow: #f3e813;
    --mail-brown: #a5652a;
    --logo-font: "Archivo", "Helvetica Neue", Arial, sans-serif;
    --detail-font: "Short Stack", "Comic Sans MS", cursive;
  }
  html, body {
    margin: 0;
    padding: 0;
    width: 1200px;
    height: 1000px;
    overflow: hidden;
    background: var(--stage);
  }
  .canvas {
    position: relative;
    width: 1200px;
    height: 1000px;
  }
  .card {
    position: absolute;
    background: var(--card-black);
    overflow: hidden;
    box-shadow: 0 10px 30px rgba(0,0,0,.35);
  }
  .card-front { left: 110px; top: 220px; width: 330px; height: 560px; }
  .card-back  { left: 520px; top: 335px; width: 560px; height: 330px; }
  .card-shape { position: absolute; inset: 0; width: 100%; height: 100%; }
  .card-shape .swoosh { fill: var(--card-white); }
  .card-shape .email-line {
    fill: var(--mail-brown);
    font-family: var(--detail-font);
    font-size: 12px;
    letter-spacing: 1px;
  }
  .wordmark {
    position: absolute;
    margin: 0;
    font-family: var(--logo-font);
    font-weight: 800;
    color: var(--card-white);
    font-size: 100px;
    line-height: 78px;
    letter-spacing: -5px;
    white-space: nowrap;
  }
  .wordmark span { display: block; }
  .wordmark .second { padding-left: 34px; }
  .card-front .wordmark { left: 44px; top: 192px; }
  .card-back .wordmark {
    left: 330px;
    top: 32px;
    transform-origin: top left;
    transform: rotate(90deg);
  }
  .holder {
    position: absolute;
    font-family: var(--detail-font);
    color: var(--name-yellow);
    text-align: right;
    font-variant: small-caps;
    white-space: nowrap;
  }
  .holder .name { display: block; font-size: 24px; letter-spacing: 1px; line-height: 1.1; }
  .holder .role { display: block; font-size: 12px; letter-spacing: 1px; }
  .card-front .holder {
    left: 320px;
    top: 28px;
    transform-origin: top left;
    transform: rotate(90deg);
  }
  .card-back .holder { right: 30px; bottom: 44px; }
</style>
</head>
<body>
<main class="canvas">

  <section class="card card-front" aria-label="Business card front">
    <svg class="card-shape" viewBox="0 0 330 560" aria-hidden="false">
      <path class="swoosh" d="M0,415 Q230,420 330,228 L330,560 L190,560 Q60,520 0,480 Z"/>
      <path id="front-mail-path" d="M118,448 Q250,420 318,302" fill="none"/>
      <text class="email-line"><textPath href="#front-mail-path">FHJGDJHGF@DGFJHDGFJD</textPath></text>
    </svg>
    <h1 class="wordmark"><span>Tisk</span><span class="second">oro</span></h1>
    <p class="holder"><span class="name">Ghdfgj Adfkhdx</span><span class="role">position</span></p>
  </section>

  <section class="card card-back" aria-label="Business card back">
    <svg class="card-shape" viewBox="0 0 560 330">
      <path class="swoosh" d="M30,0 L130,0 Q108,262 255,330 L0,330 L0,60 Q8,18 30,0 Z"/>
      <path id="back-mail-path" d="M98,24 Q94,232 206,306" fill="none"/>
      <text class="email-line"><textPath href="#back-mail-path">FHJGDJHGF@DGFJHDGFJD</textPath></text>
    </svg>
    <h2 class="wordmark"><span>Tisk</span><span class="second">oro</span></h2>
    <p class="holder"><span class="name">Ghdfgj Adfkhdx</span><span class="role">position</span></p>
  </section>

</main>
</body>
</html>
```